Vantor Wear and Fuel is looking for a Clothing/Supplement Online Store Website!

Must be convenient, and user friendly, with vibrant colors that catch the eye!

Target Market(s)

Athletes, and Fashion Customers

Industry/Entity Type

Fitness

Coding

Coded - Design and coding required

Number of Pages Required

3 page

Font styles to use
Decorative

Colors

Designer to choose colors to be used in the design.

Requirements
Must have
• Somewhere to feature products, features to promote discounts and make announcements.
Nice to have
• My logos on each page

```html
<!DOCTYPE html>
<html lang="en">
<head>
<meta charset="utf-8">
<title>Vantor Wear and Fuel — Clothing &amp; Supplement Store</title>
<link rel="stylesheet" href="https://fonts.googleapis.com/css2?family=Poppins:wght@300;400;500;600;700&display=swap">
<style>
:root{
  --ink:#2e2e2e;
  --dark:#4b4b4b;
  --mid:#6d6d6d;
  --soft:#9a9a9a;
  --line:#d9d9d9;
  --paper:#ffffff;
  --mist:#f0f0f0;
  --earth:#4a423c;
}
*{box-sizing:border-box;margin:0;padding:0}
html,body{width:1200px;height:4458px;overflow:hidden;background:var(--paper)}
body{font-family:"Poppins",sans-serif;color:var(--ink)}
.page{position:relative;width:1200px;height:4458px;overflow:hidden}
.abs{position:absolute}
.fill{position:absolute;display:block}

.topbar{position:absolute;left:0;top:0;width:1200px;height:43px;background:var(--mist);font-size:13px}
.topbar span{position:absolute;top:12px;display:flex;align-items:center;gap:6px}
.brand{font-weight:600;color:var(--dark);letter-spacing:2px;display:flex;align-items:center;gap:10px;line-height:1}
.brand .mark{width:14px;height:14px;background:var(--dark)}
.header-brand{left:111px;top:94px;font-size:44px}
.search{left:615px;top:66px;width:230px;height:38px;border:2px solid var(--dark);border-radius:20px;font-size:14px;color:var(--mid);padding:7px 14px}
.search .btn{position:absolute;right:3px;top:3px;width:28px;height:28px;border-radius:50%;background:var(--dark)}
.icon-ring{width:36px;height:36px;border:2px solid var(--dark);border-radius:50%}
.cart-label{left:968px;top:74px;font-size:17px}
.cart-badge{left:938px;top:56px;width:22px;height:22px;border-radius:50%;background:var(--soft);color:#fff;font-size:12px;text-align:center;line-height:22px}
.nav{left:526px;top:139px;display:flex;gap:36px;font-size:14px;font-weight:500;text-transform:uppercase}
.nav a{color:var(--ink);text-decoration:none}
.nav a.current{text-decoration:underline}
.header-rule{left:0;top:184px;width:1200px;height:1px;background:var(--line)}

.hero-brand{left:111px;top:312px;font-size:82px;letter-spacing:3px}
.hero-sub{left:111px;top:424px;font-size:28px;font-weight:600;color:var(--dark);line-height:38px;text-transform:uppercase}
.pill{display:inline-block;border-radius:24px;font-weight:500;text-transform:uppercase;text-align:center}
.pill.solid{background:var(--dark);color:#fff}
.pill.outline{border:2px solid var(--dark);color:var(--ink)}
.hero-cta{left:111px;top:528px;width:112px;height:47px;line-height:47px;font-size:14px}
.sale-badge{left:412px;top:543px;width:212px;height:212px;border-radius:50%;background:var(--dark);border:6px solid #fff;box-shadow:0 0 0 2px var(--line);color:#fff;text-align:center;padding-top:52px;font-size:36px;font-weight:600;line-height:46px}

.kicker{font-size:26px;font-weight:500;color:var(--dark);text-transform:uppercase}
.headline{font-size:38px;font-weight:600;color:var(--dark);text-transform:uppercase}
.tiny-mark{width:26px;height:26px;border:3px solid var(--dark);border-radius:50%}

.promo{position:absolute;top:1039px;height:326px;background:linear-gradient(135deg,#efefef,#d6d6d6);overflow:hidden}
.promo-photo{position:absolute;top:30px;height:266px;border-radius:14px}
.promo-title{font-size:40px;font-weight:600;color:var(--dark)}
.promo-line{font-size:20px;font-weight:600;color:var(--dark);text-transform:uppercase}
.promo-btn{width:118px;height:44px;line-height:40px;font-size:14px}

.tabs{left:0;top:1470px;width:1200px;text-align:center;font-size:26px;font-weight:600}
.tabs span{margin:0 16px}
.tabs .on{text-decoration:underline;color:var(--dark)}
.product{position:absolute;top:1550px;width:222px}
.product .frame{width:222px;height:282px;border:3px solid #ececec;position:relative;background:#fff}
.product .name{margin-top:20px;font-size:17px;font-weight:500}
.product .price{margin-top:6px;font-size:16px;font-weight:600}
.product .price em{font-style:normal;font-weight:400}
.product .add{margin-top:16px;width:104px;height:38px;line-height:34px;font-size:12px}
.arrow{position:absolute;width:56px;height:56px;border:2px solid var(--dark);border-radius:50%}

.band-text{right:112px;text-align:right;color:#fff}
.band-para{font-size:14px;line-height:24px;color:#eee}

.plans-para{left:111px;top:2990px;width:510px;font-size:14px;line-height:25px}
.coupon{left:111px;top:3082px;width:372px;height:48px;border:2px solid var(--dark);border-radius:26px;font-size:16px;padding:11px 16px}
.coupon .apply{position:absolute;right:3px;top:3px;height:38px;width:106px;line-height:38px;font-size:13px}

.quote-text{left:210px;top:3664px;width:780px;text-align:center;font-size:14px;line-height:25px}

.foot-col{top:4126px;font-size:15px;line-height:25px}
.foot-col h4{font-size:20px;font-weight:600;text-transform:uppercase;margin-bottom:12px}
.contact-row{display:flex;align-items:center;gap:14px;font-size:15px}
.contact-icon{width:36px;height:36px;border:2px solid var(--dark);border-radius:50%;flex:none}
.pay{width:40px;height:22px;border-radius:4px}
</style>
</head>
<body>
<div class="page">

  <div class="topbar">
    <span style="left:111px">
      <svg width="14" height="16" viewBox="0 0 14 16"><path d="M7 1a5 5 0 0 1 5 5c0 4-5 9-5 9S2 10 2 6a5 5 0 0 1 5-5z" fill="none" stroke="#2e2e2e" stroke-width="1.5"/><circle cx="7" cy="6" r="1.8" fill="#2e2e2e"/></svg>
      418 Alder Crest Way, Tampa, FL 33602</span>
    <span style="left:558px">
      <svg width="14" height="14" viewBox="0 0 14 14"><path d="M3 1l2 3-1.5 1.5a8 8 0 0 0 5 5L10 9l3 2-1.5 2.5C6 13 1 8 .5 2.5z" fill="none" stroke="#2e2e2e" stroke-width="1.3"/></svg>
      Phone: +123 555 0188</span>
    <span style="left:903px">
      <svg width="14" height="11" viewBox="0 0 14 11"><rect x=".7" y=".7" width="12.6" height="9.6" fill="none" stroke="#2e2e2e" stroke-width="1.3"/><path d="M1 1l6 5 6-5" fill="none" stroke="#2e2e2e" stroke-width="1.3"/></svg>
      Mail: info@vantorwear.com</span>
  </div>

  <div class="abs brand header-brand"><span class="mark"></span>VANTOR</div>
  <div class="abs search">Search<span class="btn"></span></div>
  <div class="abs icon-ring" style="left:862px;top:68px"></div>
  <div class="abs icon-ring" style="left:914px;top:68px;border-radius:8px"></div>
  <div class="abs cart-badge">0</div>
  <div class="abs cart-label">CART: 0 Items</div>
  <nav class="abs nav">
    <a class="current" href="#">Home</a><a href="#">About Us</a><a href="#">Products</a><a href="#">Shop</a><a href="#">Blog</a><a href="#">Contact Us</a>
  </nav>
  <div class="abs header-rule"></div>

  <!-- hero -->
  <div class="fill" style="left:0;top:185px;width:1200px;height:700px;background:linear-gradient(180deg,#f6f6f6,#e8e8e8)"></div>
  <div class="fill" role="img" aria-label="Flat lay of a plaid scarf, grey knit sweater, glasses, lipstick, brown boots, leather backpack and wool socks" style="left:500px;top:228px;width:640px;height:540px;border-radius:18px;background:linear-gradient(135deg,#d8d4cf 0%,#c7b8a8 30%,#b97a4a 55%,#9a8f86 78%,#c9c9c9 100%)"></div>
  <svg class="fill" style="left:0;top:690px" width="1200" height="200" viewBox="0 690 1200 200">
    <polygon points="0,712 234,866 1200,700 1200,890 0,890" fill="#fff"/>
    <polygon points="0,716 234,866 1200,703 1200,716 234,884 0,740" fill="#4b4b4b"/>
  </svg>
  <div class="abs brand hero-brand"><span class="mark" style="width:22px;height:22px"></span>VANTOR</div>
  <div class="abs hero-sub">Clothing/Supplement<br>Online Store</div>
  <div class="abs pill solid hero-cta">Shop Now</div>
  <div class="abs sale-badge">SALE 50%<br>OFFER</div>

  <!-- discounts -->
  <div class="fill" role="img" aria-label="Heap of green supplement powder" style="left:0;top:860px;width:150px;height:160px;border-radius:0 80px 80px 0;background:linear-gradient(135deg,#7c8a68,#4e5c3e)"></div>
  <div class="abs tiny-mark" style="left:1040px;top:858px"></div>
  <div class="abs kicker" style="right:112px;top:910px">Discounts and</div>
  <div class="abs headline" style="right:112px;top:945px">Announcements</div>

  <div class="promo" style="left:111px;width:480px">
    <div class="promo-photo" role="img" aria-label="Blue jeans, striped tee, phone, watch and grey sneakers" style="left:178px;width:290px;background:linear-gradient(135deg,#4f6b98 0%,#8aa0c4 45%,#e8e8ec 70%,#a9a9ad 100%)"></div>
    <div class="abs promo-title" style="left:22px;top:64px">CLOTHS</div>
    <div class="abs promo-line" style="left:22px;top:124px">and</div>
    <div class="abs promo-line" style="left:22px;top:162px">Apparels</div>
    <div class="abs pill outline promo-btn" style="left:22px;top:218px">Get Now</div>
  </div>
  <div class="promo" style="left:610px;width:478px">
    <div class="promo-photo" role="img" aria-label="Pink puffer jacket, knit top, jeans and black loafers" style="left:12px;width:280px;background:linear-gradient(135deg,#e4b4ab 0%,#cf958c 45%,#7e95b4 75%,#3a3a3a 100%)"></div>
    <div class="abs promo-title" style="right:24px;top:66px">GET</div>
    <div class="abs promo-line" style="right:24px;top:124px">Exclusive</div>
    <div class="abs promo-line" style="right:24px;top:162px">Offers</div>
    <div class="abs pill outline promo-btn" style="right:24px;top:218px">Get Now</div>
  </div>
  <div class="fill" role="img" aria-label="Lemon half" style="left:276px;top:1365px;width:100px;height:48px;border-radius:0 0 50px 50px;background:#f2c300"></div>

  <!-- featured -->
  <div class="abs" style="left:0;top:1440px;width:1200px;text-align:center;font-size:14px;text-transform:uppercase">Featured Products</div>
  <div class="abs tabs"><span class="on">MEN</span><span>WOMEN</span></div>

  <div class="arrow" style="left:29px;top:1704px"><svg width="52" height="52" viewBox="0 0 52 52"><path d="M30 16l-10 10 10 10M34 16l-10 10 10 10" fill="none" stroke="#4b4b4b" stroke-width="1.6"/></svg></div>
  <div class="arrow" style="left:1115px;top:1704px"><svg width="52" height="52" viewBox="0 0 52 52"><path d="M22 16l10 10-10 10M18 16l10 10-10 10" fill="none" stroke="#4b4b4b" stroke-width="1.6"/></svg></div>

  <div class="product" style="left:111px">
    <div class="frame"><div class="fill" role="img" aria-label="Stack of folded pastel sweatshirts" style="left:31px;top:85px;width:160px;height:105px;border-radius:12px;background:linear-gradient(180deg,#9aa8b4 0 30%,#8ec7c4 30% 55%,#e98aa6 55%)"></div></div>
    <div class="name">NEMO ENIM IPSAM</div>
    <div class="price">$68 <em>FROM</em> $52</div>
    <div class="pill outline add">Add to Cart</div>
  </div>
  <div class="product" style="left:362px">
    <div class="frame"><div class="fill" role="img" aria-label="White polo shirt" style="left:41px;top:55px;width:140px;height:170px;border-radius:16px;background:linear-gradient(180deg,#f6f6f6,#e2e2e2)"></div></div>
    <div class="name">NEMO ENIM IPSAM</div>
    <div class="price">$68 <em>FROM</em> $52</div>
    <div class="pill outline add">Add to Cart</div>
  </div>
  <div class="product" style="left:613px">
    <div class="frame"><div class="fill" role="img" aria-label="Black bomber jacket with grey sleeves" style="left:31px;top:55px;width:160px;height:170px;border-radius:16px;background:linear-gradient(90deg,#9a9a9a,#2c2c2c 30%,#2c2c2c 70%,#9a9a9a)"></div></div>
    <div class="name">NEMO ENIM IPSAM</div>
    <div class="price">$68 <em>FROM</em> $52</div>
    <div class="pill outline add">Add to Cart</div>
  </div>
  <div class="product" style="left:864px">
    <div class="frame"><div class="fill" role="img" aria-label="Folded blue denim jeans" style="left:31px;top:90px;width:160px;height:100px;border-radius:8px;background:linear-gradient(135deg,#2c4570,#4a6a9e)"></div></div>
    <div class="name">NEMO ENIM IPSAM</div>
    <div class="price">$68 <em>FROM</em> $52</div>
    <div class="pill outline add">Add to Cart</div>
  </div>
  <div class="fill" role="img" aria-label="Pile of yellow herbal powder" style="left:1125px;top:1965px;width:75px;height:110px;border-radius:55px 0 0 55px;background:#c9c07a"></div>

  <!-- supplements band -->
  <svg class="fill" style="left:0;top:2090px" width="1200" height="660" viewBox="0 2090 1200 660" role="img" aria-label="Dark stone table with tomatoes, avocado, lemons, nuts, mushrooms, olive oil, beans and herbs">
    <defs>
      <linearGradient id="table" x1="0" y1="0" x2="0" y2="1">
        <stop offset="0" stop-color="#4a423c"/>
        <stop offset=".5" stop-color="#554a42"/>
        <stop offset=".7" stop-color="#7a6a3a"/>
        <stop offset=".85" stop-color="#8a5a3c"/>
        <stop offset="1" stop-color="#4e6a34"/>
      </linearGradient>
    </defs>
    <polygon points="0,2235 961,2108 1200,2200 1200,2597 234,2727 0,2597" fill="url(#table)"/>
    <polygon points="0,2222 961,2095 1200,2190 1200,2200 961,2115 0,2238" fill="#4b4b4b"/>
    <polygon points="0,2597 234,2727 1200,2597 1200,2610 234,2745 0,2615" fill="#4b4b4b"/>
    <polygon points="0,2615 234,2745 1200,2610 1200,2750 0,2750" fill="#f0f0f0"/>
  </svg>
  <div class="abs tiny-mark" style="left:1038px;top:2218px;border-color:#fff"></div>
  <div class="abs band-text kicker" style="top:2266px;color:#fff">Get Exclusive</div>
  <div class="abs band-text headline" style="top:2306px;color:#fff;font-size:42px">Nutrition Supplements</div>
  <div class="abs band-text band-para" style="top:2378px;width:640px">Aliquam semper elit sit amet lorem commodo, at feugiat sapien fermen tum. Quisque iaculis, eros a interdum hendrerit, nulla lectus suscipit nisi, vitae sagittis.</div>

  <!-- plans -->
  <div class="fill" style="left:0;top:2748px;width:1200px;height:552px;background:var(--mist)"></div>
  <div class="abs tiny-mark" style="left:111px;top:2830px"></div>
  <div class="abs kicker" style="left:111px;top:2880px">Nutrition Plans</div>
  <div class="abs headline" style="left:111px;top:2915px">Choose Your Nutrition</div>
  <div class="abs plans-para">Aliquam semper elit sit amet lorem commodo, at feugiat sapien fermen tum. Quisque iaculis, eros a interdum hendrerit, nulla lectus suscipit nisi, vitae sagittis ipsum nunc id sem.</div>
  <div class="abs coupon">SHOP76868<span class="pill solid apply">Apply Code</span></div>
  <div class="abs pill solid" style="left:111px;top:3160px;width:112px;height:47px;line-height:47px;font-size:14px">Order Now</div>
  <div class="abs pill outline" style="left:232px;top:3160px;width:112px;height:47px;line-height:43px;font-size:14px">Shop Now</div>
  <div class="fill" role="img" aria-label="Ring of white bowls filled with spices, berries, vegetables and herbs" style="left:650px;top:2745px;width:500px;height:500px;border-radius:50%;background:radial-gradient(circle,#d7c08e 0%,#b5874e 40%,#7f935a 62%,#c4553f 84%,#a2453a 100%)"></div>
  <div class="fill" style="left:810px;top:2905px;width:180px;height:180px;border-radius:50%;background:#fff"></div>
  <div class="abs brand" style="left:838px;top:2985px;font-size:26px"><span class="mark" style="width:10px;height:10px"></span>VANTOR</div>

  <!-- testimonials -->
  <div class="fill" role="img" aria-label="Pink dragon fruit slice" style="left:0;top:3360px;width:52px;height:150px;border-radius:0 75px 75px 0;background:#e86a8e"></div>
  <div class="fill" role="img" aria-label="Orange papaya slice" style="left:1135px;top:3430px;width:65px;height:150px;border-radius:75px 0 0 75px;background:#f2a23a"></div>
  <div class="abs tiny-mark" style="left:586px;top:3393px"></div>
  <div class="abs kicker" style="left:0;top:3443px;width:1200px;text-align:center">Testimonials</div>
  <div class="abs headline" style="left:0;top:3478px;width:1200px;text-align:center;font-size:34px">What Our Clients Say</div>
  <div class="abs" style="left:0;top:3580px;width:1200px;text-align:center;font-size:110px;font-weight:700;line-height:110px;color:var(--dark)">&rdquo;</div>
  <div class="abs quote-text">Aliquam semper elit sit amet lorem commodo, at feugiat sapien fermen tum. Quisque iaculis, eros a interdum hendrerit, nulla lectus suscipit nisi, vitae sagittis ipsum nunc id sem.</div>
  <div class="arrow" style="left:29px;top:3657px"><svg width="52" height="52" viewBox="0 0 52 52"><path d="M30 16l-10 10 10 10M34 16l-10 10 10 10" fill="none" stroke="#4b4b4b" stroke-width="1.6"/></svg></div>
  <div class="arrow" style="left:1115px;top:3657px"><svg width="52" height="52" viewBox="0 0 52 52"><path d="M22 16l10 10-10 10M18 16l10 10-10 10" fill="none" stroke="#4b4b4b" stroke-width="1.6"/></svg></div>
  <div class="fill" role="img" aria-label="Client portrait" style="left:561px;top:3737px;width:76px;height:76px;border-radius:50%;background:linear-gradient(160deg,#9a6a4e,#d9b49a)"></div>
  <div class="abs" style="left:0;top:3828px;width:1200px;text-align:center;font-size:16px;font-weight:600">mara lind</div>

  <!-- footer -->
  <svg class="fill" style="left:0;top:3900px" width="1200" height="558" viewBox="0 3900 1200 558">
    <polygon points="0,4061 961,3910 1200,4069 1200,4458 0,4458" fill="#f0f0f0"/>
    <polygon points="0,4050 961,3905 1200,4060 1200,4072 961,3922 0,4066" fill="#4b4b4b"/>
  </svg>
  <div class="fill" role="img" aria-label="Kiwi halves" style="left:0;top:3960px;width:130px;height:110px;border-radius:55px;background:linear-gradient(135deg,#b8d44a,#6f9226)"></div>
  <div class="fill" role="img" aria-label="Bowl of green powder" style="left:1110px;top:3905px;width:90px;height:120px;border-radius:60px 0 0 60px;background:#5a7a3a"></div>

  <div class="abs brand" style="left:111px;top:4205px;font-size:36px"><span class="mark" style="width:12px;height:12px"></span>VANTOR</div>
  <div class="abs foot-col" style="left:397px">
    <h4>Categories</h4>Home<br>About Us<br>Blog<br>Nutrition<br>Pages<br>Contact Us
  </div>
  <div class="abs foot-col" style="left:601px">
    <h4>Customer Care</h4>My Account<br>Track your Order<br>Returns / Exchange<br>Support
  </div>
  <div class="abs foot-col" style="left:833px">
    <h4>Our Contact</h4>
    <div class="contact-row" style="margin-top:4px"><span class="contact-icon"></span><span style="font-size:14px;line-height:20px">418 Alder Crest Way, Tampa,<br>FL 33602</span></div>
    <div class="contact-row" style="margin-top:14px"><span class="contact-icon"></span>info@vantorwear.com</div>
    <div class="contact-row" style="margin-top:14px"><span class="contact-icon"></span>+123 555 0188</div>
  </div>
  <div class="fill" style="left:111px;top:4364px;width:977px;height:1px;background:var(--soft)"></div>
  <div class="abs" style="left:111px;top:4398px;font-size:14px">Copyright © 2019 Vantor. All Right Reserved.</div>
  <div class="abs" style="left:921px;top:4378px;width:166px;height:50px;background:#fff;border:1px solid var(--line);border-radius:4px;padding:6px 8px;display:flex;gap:6px;align-items:center">
    <span class="pay" style="background:#2a4a9a"></span>
    <span class="pay" style="background:#e07a20"></span>
    <span class="pay" style="background:#3a7ac4"></span>
  </div>
</div>
</body>
</html>
```